Flip Book Reference Guide for Medical Offices

We are looking to take a PowerPoint presentation and turn it into a flip book for our front office staff to use as a quick reference when needed. We are hoping for someone to take a quick once over of the PowerPoint then take it to the next level and make it look beautiful and professional. Alignment, graphics and clarity of design can make or break these sorts of products… we have the message, now need to ensure it's received and that is where you will come into play.

Industry/Entity Type

Medical

```html
<!DOCTYPE html>
<html lang="en">
<head>
<meta charset="utf-8">
<title>Every Patient Every Time – Front Office Reference</title>
<link rel="stylesheet" href="https://fonts.googleapis.com/css2?family=Raleway:wght@300;800&family=Montserrat:wght@400;700;800&display=swap">
<style>
  :root {
    --orange: #f7941d;
    --orange-deep: #e8671c;
    --yellow: #f6b71b;
    --navy: #1d3f5e;
    --blue: #1a8fc9;
    --teal: #2bb3c0;
    --ink: #2b2b2b;
    --muted: #444;
    --slate: #3a4a5a;
    --white: #ffffff;
  }
  * { box-sizing: border-box; margin: 0; padding: 0; }
  html, body { width: 1200px; height: 900px; overflow: hidden; background: var(--white); }
  .card {
    position: relative; width: 1200px; height: 900px; overflow: hidden;
    font-family: "Montserrat", Arial, sans-serif; color: var(--ink);
  }
  .photo-backdrop {
    position: absolute; inset: 0;
    background:
      radial-gradient(ellipse 420px 560px at 1010px 420px, rgba(200,215,225,0.55), rgba(255,255,255,0) 70%),
      radial-gradient(ellipse 300px 500px at 110px 420px, rgba(190,200,210,0.35), rgba(255,255,255,0) 70%),
      linear-gradient(90deg, #f4f6f8 0%, #fbfbfc 45%, #eef2f5 100%);
  }
  .colour-field-top {
    position: absolute; left: 0; top: 0; width: 1200px; height: 90px;
    background: linear-gradient(90deg, var(--navy) 0%, var(--blue) 25%, var(--teal) 50%, var(--yellow) 75%, var(--orange) 100%);
    -webkit-mask-image: linear-gradient(to bottom, #000 30%, transparent 100%);
    mask-image: linear-gradient(to bottom, #000 30%, transparent 100%);
  }
  .colour-field-bottom {
    position: absolute; left: 0; bottom: 0; width: 1200px; height: 170px;
    background: linear-gradient(90deg, var(--navy) 0%, var(--blue) 18%, var(--teal) 40%, var(--yellow) 62%, var(--orange) 80%, var(--orange-deep) 100%);
    -webkit-mask-image: linear-gradient(to top, #000 45%, transparent 100%);
    mask-image: linear-gradient(to top, #000 45%, transparent 100%);
  }
  .headline {
    position: absolute; left: 116px; top: 92px;
    font-family: "Raleway", Arial, sans-serif; font-size: 68px; line-height: 1;
    color: var(--slate); font-weight: 300; letter-spacing: -0.5px;
  }
  .headline strong { font-weight: 800; color: var(--orange); }
  .checklist { list-style: none; }
  .step { position: absolute; left: 114px; display: flex; gap: 16px; }
  .step-icon { width: 40px; height: 40px; flex: none; margin-top: -6px; }
  .step-title { font-size: 21px; font-weight: 800; color: #333; line-height: 1.25; }
  .step-title.wide { font-size: 20.6px; }
  .step-note { font-size: 19px; font-weight: 400; color: var(--muted); line-height: 1.3; }
  .fields { list-style: none; margin-top: 4px; }
  .fields li { font-size: 19px; font-weight: 700; color: #333; line-height: 1.5; }
  .fields li span { font-weight: 400; }
  .fields .hint { font-weight: 400; font-style: italic; font-size: 17px; }
  .fields .arrow { color: var(--orange); font-weight: 700; }
  .fields .sub { display: block; font-weight: 400; font-style: italic; font-size: 17px; padding-left: 20px; line-height: 1.2; }
  .brand {
    position: absolute; right: 48px; bottom: 50px;
    display: flex; align-items: center; gap: 10px;
    font-family: "Montserrat", Arial, sans-serif; font-weight: 700; font-size: 30px; color: var(--white);
  }
  .brand-dot { width: 22px; height: 22px; border-radius: 50%; background: var(--white); }
</style>
</head>
<body>
<main class="card">
  <div class="photo-backdrop" role="img" aria-label="Softly faded photo of a smiling doctor with a stethoscope greeting a patient"></div>
  <div class="colour-field-top" role="img" aria-label="Decorative band of blue, teal, yellow and orange tones"></div>
  <div class="colour-field-bottom" role="img" aria-label="Decorative band of blue, teal, yellow and orange tones"></div>

  <h1 class="headline">Every Patient <strong>Every Time</strong></h1>

  <ol class="checklist">
    <li class="step" style="top:176px">
      <svg class="step-icon" viewBox="0 0 40 40"><circle cx="20" cy="20" r="20" fill="var(--orange)"/><rect x="10" y="13" width="20" height="14" rx="2" fill="none" stroke="#fff" stroke-width="2"/><circle cx="15" cy="19" r="2" fill="#fff"/><path d="M20 18h7M20 22h6" stroke="#fff" stroke-width="2"/></svg>
      <div><p class="step-title">Scan insurance card(s) and verify name</p><p class="step-note">Name in PatientLog = Name on insurance card</p></div>
    </li>
    <li class="step" style="top:250px">
      <svg class="step-icon" viewBox="0 0 40 40"><circle cx="20" cy="20" r="20" fill="var(--orange)"/><path d="M13 9h11l5 5v17H13z" fill="none" stroke="#fff" stroke-width="2"/><circle cx="20" cy="21" r="4" fill="none" stroke="#fff" stroke-width="2"/><path d="M23 24l3 3" stroke="#fff" stroke-width="2"/></svg>
      <div>
        <p class="step-title wide">For new patients the following MUST be obtained @ time of scheduling:</p>
        <ul class="fields">
          <li>- Name</li>
          <li>- DOB</li>
          <li>- Phone Number including Type (home/cell/work) &amp; email <span class="hint">(Mark preferred for both)</span></li>
          <li>- Notification Preference</li>
          <li>- Insurance <span class="arrow">&gt;</span> <span>Address (on back of card)</span> <span class="arrow">&gt;</span> <span>Subscriber ID</span>
            <span class="sub">IF difference that patient collect name and DOB for subscriber</span></li>
        </ul>
      </div>
    </li>
    <li class="step" style="top:456px">
      <svg class="step-icon" viewBox="0 0 40 40"><circle cx="20" cy="20" r="20" fill="var(--orange)"/><rect x="11" y="10" width="18" height="21" rx="2" fill="none" stroke="#fff" stroke-width="2"/><path d="M14 16l2 2 3-3M14 24l2 2 3-3M22 17h4M22 25h4" stroke="#fff" stroke-width="2" fill="none"/></svg>
      <p class="step-title">Verify eligibility, co-payment, and/or deductible/co insurance</p>
    </li>
    <li class="step" style="top:492px">
      <svg class="step-icon" viewBox="0 0 40 40"><circle cx="20" cy="20" r="20" fill="var(--orange)"/><circle cx="20" cy="15" r="5" fill="#fff"/><path d="M10 30c1-6 5-8 10-8s9 2 10 8z" fill="#fff"/></svg>
      <div><p class="step-title">Verify patient account is current</p><p class="step-note">Collect any outstanding balance<br>Contact extension 305 or 418 for questions/concerns</p></div>
    </li>
    <li class="step" style="top:590px">
      <svg class="step-icon" viewBox="0 0 40 40"><circle cx="20" cy="20" r="20" fill="var(--orange)"/><rect x="15" y="9" width="11" height="18" rx="2" fill="none" stroke="#fff" stroke-width="2"/><path d="M11 24c2 4 5 7 10 7h3" stroke="#fff" stroke-width="2.5" fill="none"/></svg>
      <p class="step-title">Collect co-pay or contracted amount (if applicable)</p>
    </li>
    <li class="step" style="top:638px">
      <svg class="step-icon" viewBox="0 0 40 40"><circle cx="20" cy="20" r="20" fill="var(--orange)"/><circle cx="20" cy="20" r="8" fill="none" stroke="#fff" stroke-width="4" stroke-dasharray="4 2.3"/><circle cx="20" cy="20" r="3" fill="#fff"/></svg>
      <p class="step-title">Confirm patient’s preferred pharmacy is enter in with an (eRx)</p>
    </li>
    <li class="step" style="top:686px">
      <svg class="step-icon" viewBox="0 0 40 40"><circle cx="20" cy="20" r="20" fill="var(--orange)"/><rect x="11" y="10" width="16" height="20" rx="1" fill="none" stroke="#fff" stroke-width="2"/><path d="M14 16h9M14 20h6M22 27l8-9 2 2-8 9h-2z" stroke="#fff" stroke-width="2" fill="none"/></svg>
      <p class="step-title">Print and have patient sign all required areas of the registration form</p>
    </li>
  </ol>

  <div class="brand"><span class="brand-dot"></span>BrightWell Care</div>
</main>
</body>
</html>
```